Business Card Design Project - del varosi group

dear Sirs

we need business card design for our group ( DEL Varosi Group ) , i have got the Logo design of our group from pixel harbor in previous , so all need details relating to our group i think available with you, as well as the the chosen logo design

we hope to provide us with business card logo that to be appropaite and satisfactory to us .

thanks

note : logo design of our group is attached .
Updates

Reason: please extend the deadline of my project for additional 15 days because i didn't received appropriate design for our gruop yet . kindly beaware that i have received 77 design till now , supossed to send me 200-250 design at least . thanks

Target Market(s)

contents

name : Kerem EL Nadiri

position : Operation Manager

Industry/Entity Type

Business

Requirements
Must have

• person name

group logo
Nice to have
• logo color matching with back background

```html
<!DOCTYPE html>
<html lang="en">
<head>
<meta charset="utf-8">
<title>DEL Varosi Group – Business Card</title>
<link rel="stylesheet" href="https://fonts.googleapis.com/css2?family=Noto+Serif:wght@700&family=Open+Sans:wght@400;600&display=swap">
<style>
  :root {
    --page-bg: #e4e6e9;
    --card-dark: #1c1c1d;
    --card-dark-edge: #0c0c0d;
    --card-dark-glow: #2f2f31;
    --band-blue: #0f4d96;
    --band-blue-deep: #0b3d7a;
    --band-edge: #3a6fb5;
    --name-blue: #1a56a8;
    --title-grey: #c9c9c9;
    --contact-white: #ffffff;
    --mark-muted: #4a5064;
  }
  * { margin: 0; padding: 0; box-sizing: border-box; }
  html, body { width: 1067px; height: 1200px; overflow: hidden; }
  body {
    background: var(--page-bg);
    font-family: "Open Sans", Arial, sans-serif;
    position: relative;
  }
  .card {
    position: absolute;
    left: 153px;
    width: 760px;
    height: 434px;
    overflow: hidden;
    box-shadow: 0 10px 28px rgba(0,0,0,.28);
  }
  .card--front {
    top: 118px;
    background: radial-gradient(ellipse at 50% 20%, var(--card-dark-glow) 0%, var(--card-dark) 45%, var(--card-dark-edge) 100%);
  }
  .card--back {
    top: 648px;
    background: radial-gradient(ellipse at 50% 50%, var(--card-dark-glow) 0%, var(--card-dark) 50%, var(--card-dark-edge) 100%);
  }
  .band { position: absolute; inset: 0; width: 100%; height: 100%; }
  .holder {
    position: absolute;
    right: 40px;
    top: 30px;
    text-align: right;
  }
  .holder__name {
    font-family: "Noto Serif", Georgia, serif;
    font-weight: 700;
    font-size: 36px;
    color: var(--name-blue);
    line-height: 1.1;
  }
  .holder__title {
    font-size: 20px;
    color: var(--title-grey);
    margin-top: 4px;
  }
  .group-mark {
    position: absolute;
    left: 26px;
    top: 120px;
    display: flex;
    align-items: center;
    gap: 12px;
  }
  .group-mark__square {
    width: 18px; height: 18px;
    background: var(--band-edge);
  }
  .group-mark__name {
    font-weight: 600;
    font-size: 30px;
    letter-spacing: 1px;
    color: var(--band-edge);
  }
  .contact {
    position: absolute;
    right: 40px;
    bottom: 30px;
    text-align: right;
    color: var(--contact-white);
    font-size: 18px;
    line-height: 1.4;
  }
  .contact__value { font-weight: 600; }
  .back-mark {
    position: absolute;
    inset: 0;
    display: flex;
    align-items: center;
    justify-content: center;
    gap: 18px;
  }
  .back-mark__square {
    width: 30px; height: 30px;
    background: var(--mark-muted);
  }
  .back-mark__name {
    font-weight: 600;
    font-size: 54px;
    letter-spacing: 2px;
    color: var(--mark-muted);
  }
</style>
</head>
<body>
  <section class="card card--front">
    <svg class="band" viewBox="0 0 760 434" preserveAspectRatio="none" aria-hidden="true">
      <defs>
        <linearGradient id="bandFill" x1="0" y1="0" x2="0" y2="1">
          <stop offset="0" stop-color="var(--band-blue)"/>
          <stop offset="1" stop-color="var(--band-blue-deep)"/>
        </linearGradient>
      </defs>
      <polygon points="0,168 305,312 760,160 760,434 0,434" fill="url(#bandFill)"/>
      <polyline points="0,168 305,312 760,160" fill="none" stroke="var(--band-edge)" stroke-width="2"/>
    </svg>
    <div class="holder">
      <p class="holder__name">Kerem EL Nadiri</p>
      <p class="holder__title">Operation Manager</p>
    </div>
    <div class="group-mark">
      <span class="group-mark__square"></span>
      <span class="group-mark__name">DEL VAROSI GROUP</span>
    </div>
    <div class="contact">
      <p>Phone: <span class="contact__value">0123 456 789</span></p>
      <p>Fax: <span class="contact__value">0123 456 789</span></p>
      <p>info@yourdomain.com</p>
      <p>www.yourdomain.com</p>
      <p>PO. Box: City name, etc.</p>
    </div>
  </section>

  <section class="card card--back">
    <div class="back-mark">
      <span class="back-mark__square"></span>
      <span class="back-mark__name">DEL VAROSI GROUP</span>
    </div>
  </section>
</body>
</html>
```